The design should look similar to the uploaded example to accommodate the information needed for a business card template. I would like to see the colors orange and charcoal grey incorporated along with the logo.The following should be on the back of the card SPECIALIZING IN NEW AND USED TIRES & WHEELS FOR:- Loaders- Skid Steers- Telehandlers- Boom Lifts- Forklifs and moreELIMINATING DOWNTIMEWheel Exchange Program for New & Used Foam Filled and Solid Rubber TiresSPECIALTY SERVICES- Foam Filling Tires- Largest Tire Press in SE- ONSITE Forklift Tire Press- Boom Truck Services - Rubber Tracks

Target Market(s)

New and Existing Customers

Industry/Entity Type

Business

Contact Information for Business Card

NAMEHEAVY DUTY TIRE, LLC8470 Belvedere RoadWest Palm Beach, FL 33411P: 844-HD-TIRESF: 561-431-6469C:E: W: WWW.GRANITERIMSUPPLY-EXAMPLE.COM

Font styles to use
Sans Serif

Colors
f37122
333333

Requirements
Must have
• The logo and the information indicated for the backside of the card
Nice to have
• Keep the orange and charcoal grey colors

```html
<!DOCTYPE html>
<html lang="en">
<head>
<meta charset="utf-8">
<title>Granite Rim Supply, LLC — Business Card</title>
<link href="https://fonts.googleapis.com/css2?family=Alfa+Slab+One&family=Didact+Gothic&display=swap" rel="stylesheet">
<style>
  :root {
    --orange: #f89c4f;
    --charcoal: #333333;
    --rule: #4a4f55;
    --paper: #ffffff;
    --backdrop: #d9d9d9;
    --ink: #1e1e1e;
    --badge: #c9c9c9;
  }
  * { margin: 0; padding: 0; box-sizing: border-box; }
  html, body { width: 1189px; height: 1200px; overflow: hidden; }
  body {
    background: var(--backdrop);
    font-family: "Didact Gothic", "Century Gothic", sans-serif;
    color: var(--ink);
    position: relative;
  }
  .card {
    position: absolute;
    left: 140px;
    width: 917px;
    height: 524px;
    background: var(--paper);
    box-shadow: 0 6px 14px rgba(0,0,0,0.35);
    overflow: hidden;
  }
  .card--front { top: 45px; }
  .card--back { top: 600px; }

  /* Front */
  .band {
    position: absolute;
    left: 0; right: 0;
    top: 43px;
    height: 192px;
    background: var(--orange);
    border-top: 4px solid var(--rule);
    border-bottom: 4px solid var(--rule);
  }
  .brand-disc {
    position: absolute;
    border-radius: 50%;
    background: var(--charcoal);
    display: flex;
    align-items: center;
    justify-content: center;
    text-align: center;
    color: var(--paper);
    font-family: "Alfa Slab One", serif;
    line-height: 1.05;
  }
  .brand-disc--front {
    left: 341px; top: 17px;
    width: 236px; height: 236px;
    font-size: 30px;
  }
  .brand-disc--back {
    left: 49px; top: 38px;
    width: 156px; height: 156px;
    font-size: 20px;
  }
  .company-name {
    position: absolute;
    left: 0; right: 0;
    top: 264px;
    text-align: center;
    font-family: "Alfa Slab One", serif;
    font-size: 36px;
    letter-spacing: 2px;
    word-spacing: 6px;
    color: #111;
  }
  .contact-list { list-style: none; position: absolute; left: 68px; top: 316px; }
  .contact-list li {
    display: flex;
    align-items: center;
    height: 31px;
    font-size: 23px;
    letter-spacing: 0.8px;
    white-space: nowrap;
  }
  .contact-list svg { width: 17px; height: 17px; margin-right: 24px; flex: none; }

  /* Back */
  .section-title {
    position: absolute;
    left: 290px;
    top: 62px;
    font-size: 51px;
    letter-spacing: 1.2px;
    font-weight: 400;
    line-height: 1;
    color: #111;
    white-space: nowrap;
  }
  .section-rule {
    position: absolute;
    left: 202px; right: 0;
    top: 117px;
    height: 3px;
    background: var(--rule);
  }
  .service-list { list-style: none; position: absolute; left: 118px; top: 230px; }
  .service-list li {
    display: flex;
    align-items: center;
    height: 48px;
    font-size: 30px;
    letter-spacing: 0.8px;
    white-space: nowrap;
  }
  .service-list li:nth-child(3),
  .service-list li:nth-child(4) { height: 50px; }
  .service-list svg { width: 18px; height: 18px; margin-right: 24px; flex: none; }
  .badge { position: absolute; }
  .badge--circle { left: 620px; top: 378px; width: 86px; height: 80px; }
  .badge--triangle { left: 740px; top: 368px; width: 112px; height: 92px; }
</style>
</head>
<body>

<section class="card card--front" aria-label="Card front">
  <div class="band"></div>
  <div class="brand-disc brand-disc--front">GRANITE<br>RIM</div>
  <h1 class="company-name">GRANITE RIM SUPPLY LLC</h1>
  <ul class="contact-list">
    <li><svg viewBox="0 0 16 16"><rect width="16" height="16" rx="2" fill="#555"/><path d="M5 3.5c-1 .6-1.4 2-.6 3.8.9 2 2.6 4 4.4 5 1.3.6 2.4.3 3-.5l-1.6-1.6-1.2.7C8 10.2 6.7 8.6 6 7l.8-1.1z" fill="#fff"/></svg>844-GR-WHEEL</li>
    <li><svg viewBox="0 0 16 16"><rect width="16" height="16" rx="2" fill="#555"/><rect x="5" y="2.5" width="6" height="11" rx="1" fill="#fff"/><rect x="6" y="4" width="4" height="6" fill="#555"/></svg>841-362-7180</li>
    <li><svg viewBox="0 0 16 16"><rect width="16" height="16" rx="2" fill="#555"/><rect x="3" y="6" width="10" height="5" fill="#fff"/><rect x="5" y="3" width="6" height="3" fill="#fff"/><rect x="5" y="10" width="6" height="3" fill="#ddd"/></svg>561-278-9053</li>
    <li><svg viewBox="0 0 16 16"><rect width="16" height="16" rx="2" fill="#555"/><circle cx="8" cy="8" r="5" fill="none" stroke="#fff" stroke-width="1.4"/><path d="M3 8h10M8 3c-2 2.5-2 7.5 0 10M8 3c2 2.5 2 7.5 0 10" fill="none" stroke="#fff" stroke-width="1"/></svg>www.graniterimsupply-example.com</li>
    <li><svg viewBox="0 0 16 16"><rect width="16" height="16" rx="2" fill="#555"/><rect x="3" y="4.5" width="10" height="7" fill="#fff"/><path d="M3 4.5l5 4 5-4" fill="none" stroke="#555" stroke-width="1"/></svg>info@graniterimsupply-example.com</li>
    <li><svg viewBox="0 0 16 16"><rect width="16" height="16" rx="2" fill="#555"/><path d="M8 2.5a3.5 3.5 0 0 1 3.5 3.5c0 2.6-3.5 7-3.5 7S4.5 8.6 4.5 6A3.5 3.5 0 0 1 8 2.5z" fill="#fff"/><circle cx="8" cy="6" r="1.3" fill="#555"/></svg>5126 Marston Lane Cedar Bluff ,Florida 33480</li>
  </ul>
</section>

<section class="card card--back" aria-label="Card back">
  <div class="brand-disc brand-disc--back">GRANITE<br>RIM</div>
  <div class="section-rule"></div>
  <h2 class="section-title">SPECIALTY SERVICES</h2>
  <ul class="service-list">
    <li><svg viewBox="0 0 18 18"><circle cx="9" cy="9" r="5" fill="none" stroke="#555" stroke-width="1.3"/><circle cx="9" cy="9" r="2" fill="#333"/><path d="M9 1v4M9 13v4M1 9h4M13 9h4" stroke="#555" stroke-width="1.2"/></svg>Rubber Tracks</li>
    <li><svg viewBox="0 0 18 18"><circle cx="9" cy="9" r="5" fill="none" stroke="#555" stroke-width="1.3"/><circle cx="9" cy="9" r="2" fill="#333"/><path d="M9 1v4M9 13v4M1 9h4M13 9h4" stroke="#555" stroke-width="1.2"/></svg>Foam Filling Tires</li>
    <li><svg viewBox="0 0 18 18"><circle cx="9" cy="9" r="5" fill="none" stroke="#555" stroke-width="1.3"/><circle cx="9" cy="9" r="2" fill="#333"/><path d="M9 1v4M9 13v4M1 9h4M13 9h4" stroke="#555" stroke-width="1.2"/></svg>Largest Tire Press in SE</li>
    <li><svg viewBox="0 0 18 18"><circle cx="9" cy="9" r="5" fill="none" stroke="#555" stroke-width="1.3"/><circle cx="9" cy="9" r="2" fill="#333"/><path d="M9 1v4M9 13v4M1 9h4M13 9h4" stroke="#555" stroke-width="1.2"/></svg>ONSITE Forklift Tire Press</li>
    <li><svg viewBox="0 0 18 18"><circle cx="9" cy="9" r="5" fill="none" stroke="#555" stroke-width="1.3"/><circle cx="9" cy="9" r="2" fill="#333"/><path d="M9 1v4M9 13v4M1 9h4M13 9h4" stroke="#555" stroke-width="1.2"/></svg>Boom Truck Services</li>
  </ul>
  <svg class="badge badge--circle" viewBox="0 0 86 80" role="img" aria-label="Trade association membership badge">
    <circle cx="43" cy="40" r="38" fill="var(--badge)"/>
  </svg>
  <svg class="badge badge--triangle" viewBox="0 0 112 92" role="img" aria-label="Rental association membership badge">
    <polygon points="56,4 106,88 6,88" fill="var(--badge)"/>
  </svg>
</section>

</body>
</html>
```